Purple Heart Veteran Owned Telecommunications Company

I need to develop my current website (brightwirel.com) into something more upbeat and modern. I created the existing one with SiteKindle and it's very basic. I'm open to using any type of website builder and not just SiteKindle. I feel like SiteKindle is pretty basic. I want something customized to me and my company. I plan on doing a Zorbix Ad, Email Marketing, and Mail Marketing campaign and SEO push. I want a website built so they can look up my company. We are a low voltage telecommunications company based out of Chicago. We are a General Contractor and I have technicians all throughout the US and Canada. I mainly appeal to the government and fortune 500 companies across the country. I focus on commercial and federal work with minor work in Residential. I need to appeal to everyone and not just locally. My company name is Brightwirel. I'm a Marine Corps veteran and my I created the company with my son in mind. We are a service disabled veteran owned small business. I'm open to any play on my logo or color scheme. I do like the color blue but I'm open to anything again. I would like a website that has little maintenance needed and something that is modern and sticks out with my competitors. I'm only in business for 2 years but I need to stick out to my competition so I can start building revenue through ads and getting my name out there with limited funds. I did have a logo and name created which I'm attaching. I'm completely open to changing it if someone can come up with something creative. I would like someone that understands SEO and can help feed work to my site. I'm also open to paying more for the right website that gets everything I want. I know I need to add more pages and more professional. Please use my website as a template but also feel free to come up with any new ideas. I would like some feedback or ideas on what else to add to my website or remove so I can appeal to my audience and look more authentic.

Target Market(s)

Commercial Companies locally in Chicago, and Fortune 500 companies and the government

Industry/Entity Type

Telecommunications

Coding

Number of Pages Required

Font styles to use
Sans Serif

Requirements
Must have
• A Modern, fresh look that is customized and original. Something that sticks out to my customers.
Nice to have
• Anything that sticks out and isn't stock. I'm open to anything that is unique and different.
Should not have
• Nothing Generic. I would like something custom tailored to my business

```html
<!DOCTYPE html>
<html lang="en">
<head>
<meta charset="utf-8">
<title>Brightwirel — General Contractor</title>
<link rel="stylesheet" href="https://fonts.googleapis.com/css2?family=Montserrat:wght@600;700;800&family=Open+Sans:wght@300;400&display=swap">
<style>
:root{
  --navy:#0c2466;
  --navy-deep:#0d2a78;
  --ink:#2b2f3a;
  --white:#ffffff;
  --sky-top:#5c78a8;
  --sky-bottom:#1b2e52;
  --mist:#dde2ea;
  --field:#c9d2bf;
  --accent:#4f82e6;
  --card-line:#c8d2e4;
}
*{box-sizing:border-box;margin:0;padding:0}
html,body{width:1200px;height:2558px;overflow:hidden}
body{position:relative;background:var(--white);font-family:"Open Sans",Arial,sans-serif;color:var(--ink)}
.abs{position:absolute}

/* header */
.site-header{left:0;top:0;width:1200px;height:115px;background:var(--white)}
.main-nav{left:0;top:48px;width:1200px;height:20px}
.main-nav a{position:absolute;font-family:"Montserrat",Arial,sans-serif;font-weight:600;font-size:14px;color:#3a3f4b;text-decoration:none;white-space:nowrap}
.main-nav a.is-active{color:var(--navy)}
.brand-pennant{left:0;top:0;z-index:5}
.brand-name{left:115px;top:70px;width:308px;text-align:center;font-family:"Montserrat",Arial,sans-serif;font-weight:700;font-size:22px;letter-spacing:1.5px;color:var(--navy);z-index:6}

/* hero */
.hero{left:0;top:115px;z-index:1}
.hero-title{left:0;top:335px;width:1200px;text-align:center;font-family:"Montserrat",Arial,sans-serif;font-weight:800;font-size:82px;line-height:1;color:var(--white);z-index:3}
.hero-sub{left:0;top:430px;width:1200px;text-align:center;font-weight:300;font-size:23px;letter-spacing:2.6px;color:var(--white);z-index:3}
.hero-arrow{top:343px;width:48px;height:48px;border-radius:50%;background:rgba(255,255,255,.12);z-index:3}
.hero-arrow svg{position:absolute;left:14px;top:12px}

/* feature cards */
.feature-card{top:820px;width:313px;height:410px;border:3px solid var(--card-line);color:var(--white);text-align:center}
.feature-card h3{position:absolute;left:0;top:150px;width:100%;font-family:"Montserrat",Arial,sans-serif;font-weight:700;font-size:21px}
.feature-card p{position:absolute;left:36px;top:186px;width:235px;font-size:16px;line-height:27px}
.card-do{left:113px;background:linear-gradient(180deg,#134a6e,#0f3b5e 70%,#0c2f4c)}
.card-together{left:448px;background:linear-gradient(180deg,#274c96,#1f4387 60%,#1b3a78)}
.card-trust{left:785px;background:linear-gradient(180deg,#34466e,#2d3f66 60%,#3a4a74)}

/* about */
.about{left:0;top:1330px;width:1200px;height:463px;background:linear-gradient(180deg,#e3e7ee 0%,#dde3e8 60%,#cfd7c8 80%,#c6d0b9 100%)}
.about h2{position:absolute;left:0;top:80px;width:1200px;text-align:center;font-family:"Montserrat",Arial,sans-serif;font-weight:700;font-size:35px;line-height:42px;color:var(--navy)}
.about p{position:absolute;left:150px;width:900px;text-align:center;font-size:16px;line-height:27px;color:#3b3f48}
.btn-learn{left:463px;top:319px;width:283px;height:45px;background:var(--navy);color:var(--white);font-family:"Montserrat",Arial,sans-serif;font-weight:700;font-size:15px;line-height:45px;text-align:center}

/* contact */
.contact{left:0;top:1792px;width:1200px;height:766px;background:linear-gradient(180deg,#0e2b7c,#10307f 60%,#132f74)}
.contact h2{position:absolute;left:0;top:54px;width:1200px;text-align:center;font-family:"Montserrat",Arial,sans-serif;font-weight:700;font-size:38px;color:var(--white)}
.contact-intro{left:200px;top:106px;width:800px;text-align:center;font-size:14.5px;line-height:24px;color:var(--white)}
.contact-line{left:778px;font-size:18px;color:#d8e0f2;display:flex;align-items:center;gap:12px}
.map-area{left:113px;top:258px;width:618px;height:384px;border:5px solid #5a73b0;background:linear-gradient(135deg,#e6e6e6,#dcdcdc 60%,#c8e6b8)}
.form-label{left:778px;font-size:12px;color:var(--white)}
.form-field{left:778px;width:319px;height:33px;background:var(--white);font-size:12px;color:#444;padding:8px 20px}
.form-message{left:778px;top:488px;width:319px;height:94px;background:var(--white);font-size:12px;color:#444;padding:12px 20px}
.btn-submit{left:973px;top:600px;width:124px;height:42px;background:var(--accent);color:var(--white);font-family:"Montserrat",Arial,sans-serif;font-weight:600;font-size:14px;line-height:42px;text-align:center}
.footer-rule{left:113px;top:711px;width:984px;height:1px;background:rgba(255,255,255,.25)}
.copyright{left:0;top:737px;width:1200px;text-align:center;font-size:12px;color:var(--white)}
.social-dot{top:726px;width:37px;height:37px;border-radius:50%;background:var(--white)}
</style>
</head>
<body>

<header class="abs site-header"></header>

<svg class="abs brand-pennant" width="440" height="270" viewBox="0 0 440 270">
  <polygon points="115,0 425,0 268,262" fill="#ffffff" stroke="#c9cdd4" stroke-width="3"/>
</svg>
<div class="abs brand-name">BRIGHTWIREL</div>

<nav class="abs main-nav">
  <a class="is-active" style="left:518px">HOME</a>
  <a style="left:612px">LOW VOLTAGE</a>
  <a style="left:764px">MARKETS</a>
  <a style="left:880px">OUR TEAM</a>
  <a style="left:1005px">CONTACT US</a>
</nav>

<svg class="abs hero" width="1200" height="656" viewBox="0 0 1200 656" role="img" aria-label="Photo of telecommunication towers silhouetted against a dusky blue sky">
  <defs>
    <linearGradient id="sky" x1="0" y1="0" x2="0" y2="1">
      <stop offset="0" stop-color="#5a76a6"/>
      <stop offset=".55" stop-color="#4b6494"/>
      <stop offset="1" stop-color="#14223f"/>
    </linearGradient>
  </defs>
  <polygon points="0,0 1200,0 1200,550 610,655 0,550" fill="url(#sky)"/>
</svg>

<div class="abs hero-arrow" style="left:31px"><svg width="20" height="24" viewBox="0 0 20 24"><polyline points="14,2 4,12 14,22" fill="none" stroke="#ffffff" stroke-width="1.5"/></svg></div>
<div class="abs hero-arrow" style="left:1119px"><svg width="20" height="24" viewBox="0 0 20 24"><polyline points="6,2 16,12 6,22" fill="none" stroke="#ffffff" stroke-width="1.5"/></svg></div>
<h1 class="abs hero-title">BRIGHTWIREL</h1>
<div class="abs hero-sub">With over 20 years of proven experience</div>

<section class="abs feature-card card-do" role="img" aria-label="Card background photo of a satellite dish in deep teal">
  <h3>WHAT WE DO</h3>
  <p>Our past projects include both new construction and repairs/restorations. Occupied and fully operational job sites are never a problem. And we can also plan, manage, and design jobs.</p>
</section>
<section class="abs feature-card card-together" role="img" aria-label="Card background photo of a city at night in blue">
  <h3>WORKING TOGETHER</h3>
  <p>We offer an end-to-end client experience that includes seamless communication, budgeting, staffing, on-site organization, and solid, quality handiwork every time.</p>
</section>
<section class="abs feature-card card-trust" role="img" aria-label="Card background photo of a handshake before office towers">
  <h3>TRUST</h3>
  <p>We are committed to building trust among our clients, contractors, colleagues, and community</p>
</section>

<section class="abs about" role="img" aria-label="Faded photo of a transmission tower over a palm-lined field">
  <h2>LEADER IN STRUCTURED CABLING, WIRING,<br>AND NETWORKING SERVICE</h2>
  <p style="top:174px">Our company has a network of subcontractors nationally and in Canada.&nbsp; We also have the ability to provide our own labor which allows us to offer a competitive edge and provide immediate assistance to our customers.</p>
  <p style="top:243px">Our Mission is to work hard every day to make Brightwirel the world's most respected company brand.</p>
  <div class="abs btn-learn">LEARN MORE INFORMATION</div>
</section>

<section class="abs contact">
  <h2>CONTACT US</h2>
  <p class="abs contact-intro">If you want to be part of a strong company culture that values professionalism, innovation, and your core values align with ours, we would love to meet you.</p>

  <div class="abs contact-line" style="top:177px">
    <svg width="16" height="16" viewBox="0 0 16 16"><path d="M3 1l3 3-2 2c1 2 3 4 5 5l2-2 3 3-2 3C7 15 1 9 1 3z" fill="#d8e0f2"/></svg>
    <span>312-555-0174</span>
  </div>
  <div class="abs contact-line" style="top:207px">
    <svg width="17" height="14" viewBox="0 0 17 14"><rect x="1" y="1" width="15" height="12" rx="1.5" fill="none" stroke="#d8e0f2" stroke-width="1.6"/><polyline points="1.5,2 8.5,8 15.5,2" fill="none" stroke="#d8e0f2" stroke-width="1.6"/></svg>
    <span>Support@brightwirel.com</span>
  </div>

  <div class="abs map-area" role="img" aria-label="Street map showing the office location with a marker"></div>

  <div class="abs form-label" style="top:262px">Enter Your Name*</div>
  <div class="abs form-field" style="top:289px">Name</div>
  <div class="abs form-label" style="top:331px">Enter Your Email*</div>
  <div class="abs form-field" style="top:358px">Email</div>
  <div class="abs form-label" style="top:400px">Enter Your Subject</div>
  <div class="abs form-field" style="top:427px">Subject</div>
  <div class="abs form-message">Type your message here..</div>
  <div class="abs btn-submit">SUBMIT NOW</div>

  <div class="abs footer-rule"></div>
  <div class="abs copyright">Copyright © 2020 Brightwirel - All Rights Reserved.</div>
  <div class="abs social-dot" style="left:1007px" aria-label="Social profile"></div>
  <div class="abs social-dot" style="left:1059px" aria-label="Social profile"></div>
</section>

</body>
</html>
```